A new presentation to our clients

we are a Real Estate agency, our website is www.lumibrasa.com and it’s time to have a new, fashion and remarcable Business Card. we want to differentiate ourselves from other companies so we want a business card that differentiates us. we want the business card to impact our customers. in the competitive market that we have today, we have to be different and it is this difference that we seek

Target Market(s)

Real Estate Clients

Contact Information for Business Card

We search a totaly diferent card from the usual

Font styles to use
Sans Serif

Colors
e34197

Requirements
Must have
• Logo, adress, phone contact, e-mail, photo, and our website
Nice to have
• We would like to see a modern business card
Should not have
• Houses or building draws

```html
<!DOCTYPE html>
<html lang="en">
<head>
<meta charset="utf-8">
<title>Lumibrasa Business Card</title>
<link rel="stylesheet" href="https://fonts.googleapis.com/css2?family=Roboto:wght@400;500&display=swap">
<style>
  :root {
    --brand-pink: #e41e73;
    --paper: #ffffff;
    --backdrop: #d6d6d6;
    --muted: #555555;
  }
  html, body {
    margin: 0;
    padding: 0;
    width: 1200px;
    height: 800px;
    overflow: hidden;
    background: var(--backdrop);
    font-family: "Roboto", Arial, sans-serif;
  }
  .stage {
    position: relative;
    width: 1200px;
    height: 800px;
  }
  .card {
    position: absolute;
    top: 245px;
    width: 540px;
    height: 310px;
    box-shadow: 0 6px 18px rgba(0, 0, 0, 0.18);
  }
  .card-front {
    left: 40px;
    background: var(--brand-pink);
    display: flex;
    align-items: center;
    justify-content: center;
  }
  .card-back {
    left: 620px;
    background: var(--paper);
  }
  .front-wordmark {
    color: var(--paper);
    font-weight: 500;
    font-size: 64px;
    letter-spacing: 1px;
  }
  .card-back svg {
    display: block;
  }
  .back-wordmark {
    fill: var(--brand-pink);
    font-family: "Roboto", Arial, sans-serif;
    font-weight: 500;
    font-size: 42px;
  }
  .person-name {
    fill: var(--brand-pink);
    font-family: "Roboto", Arial, sans-serif;
    font-weight: 500;
    font-size: 18px;
  }
  .person-role {
    fill: var(--muted);
    font-family: "Roboto", Arial, sans-serif;
    font-size: 11px;
  }
  .contact-line, .address-line {
    fill: var(--paper);
    font-family: "Roboto", Arial, sans-serif;
    font-size: 14px;
  }
  .contact-icon {
    fill: none;
    stroke: var(--paper);
    stroke-width: 1.3;
  }
</style>
</head>
<body>
<main class="stage">
  <section class="card card-front" aria-label="Card front">
    <span class="front-wordmark">Lumibrasa</span>
  </section>

  <section class="card card-back" aria-label="Card back">
    <svg width="540" height="310" viewBox="0 0 540 310" xmlns="http://www.w3.org/2000/svg">
      <polygon class="pink-field" points="0,215 540,140 540,310 0,310" fill="var(--brand-pink)"/>
      <line class="accent-rule" x1="0" y1="200" x2="490" y2="128" stroke="var(--brand-pink)" stroke-width="1.5"/>

      <text class="back-wordmark" x="40" y="128">Lumibrasa</text>

      <text class="person-name" x="490" y="118" text-anchor="end">DANIEL FERRAZ</text>
      <text class="person-role" x="490" y="142" text-anchor="end">Director</text>

      <text class="address-line" x="505" y="178" text-anchor="end">Rua das Camélias, 118</text>
      <text class="address-line" x="505" y="197" text-anchor="end">4150-042, Porto</text>

      <g class="contact-list">
        <path class="contact-icon" d="M41,234 q0,7 7,7 l1.5,-2 -2.5,-2 -1.5,1 q-2,-1 -2.5,-2.5 l1,-1.5 -2,-2.5z"/>
        <text class="contact-line" x="58" y="241">(+351) 210 458 320</text>

        <rect class="contact-icon" x="41" y="253" width="9" height="8"/>
        <line class="contact-icon" x1="43" y1="256" x2="48" y2="256"/>
        <text class="contact-line" x="58" y="261">(+351) 210 458 329</text>

        <rect class="contact-icon" x="41" y="273" width="10" height="7"/>
        <polyline class="contact-icon" points="41,273 46,277 51,273"/>
        <text class="contact-line" x="58" y="281">geral@lumibrasa.com</text>

        <circle class="contact-icon" cx="46" cy="296" r="4.5"/>
        <line class="contact-icon" x1="41.5" y1="296" x2="50.5" y2="296"/>
        <text class="contact-line" x="58" y="301">www.lumibrasa.com</text>
      </g>
    </svg>
  </section>
</main>
</body>
</html>
```